Banner Pop Up Opt In Form REDESIGNS - SLEEK BLACK LOOK

Please redesign banners attached.

I am looking for a very sleek look....I do not like this collage of images on these current designs. Please keep all content same but use images that pop.

I have an acccount at www.pixvane-example.com or you can use your own images.

I like black background for somereason because it looks very sleek....but these designs should pop , build trust and credibility and have easy opt in form....SLEEK AND MODERN LOOK is what im looking for....

Target Market(s)

Consumers on websites

Requirements
Must have
• Please redesign banners attached.

Nice to have

Should not have

```html
<!DOCTYPE html>
<html lang="en">
<head>
<meta charset="utf-8">
<title>Newsletter Opt-In Banners – Sleek Black</title>
<link rel="stylesheet" href="https://fonts.googleapis.com/css2?family=Jost:wght@400;500&family=Oswald:wght@300;400&display=swap">
<style>
  :root {
    --bg-deep: #070707;
    --bg-leather: #1c1c1c;
    --gold-light: #fbe9a0;
    --gold: #d4a22c;
    --gold-dark: #9a6a12;
    --offer-red: #c4141a;
    --button-red: #d81d1d;
    --button-red-dark: #8a0a0a;
    --field-white: #ffffff;
    --ink: #0a0a0a;
    --note-white: #f2f2f2;
    --divider: #3a3a3a;
  }
  * { box-sizing: border-box; margin: 0; padding: 0; }
  html, body { width: 1200px; height: 516px; overflow: hidden; background: var(--bg-deep); }
  .stage { position: relative; width: 1200px; height: 516px; display: flex; }
  .banner {
    position: relative; width: 600px; height: 516px; overflow: hidden;
    background:
      radial-gradient(ellipse at 60% 35%, rgba(70,70,70,.35), transparent 60%),
      radial-gradient(ellipse at 20% 80%, rgba(50,50,50,.25), transparent 55%),
      linear-gradient(160deg, var(--bg-leather), var(--bg-deep));
  }
  .banner + .banner { border-left: 1px solid var(--divider); }
  .headline { position: absolute; left: 0; top: 0; width: 600px; height: 170px; overflow: visible; }
  .headline text { font-family: 'Jost', sans-serif; font-weight: 400; }
  .pitch {
    position: absolute; left: 0; width: 600px; text-align: center;
    font-family: 'Oswald', sans-serif; font-weight: 300; text-transform: uppercase;
    white-space: nowrap; line-height: 1;
  }
  .pitch-lead { font-size: 20.6px; letter-spacing: .6px; color: var(--gold); }
  .pitch-offer { font-size: 20px; letter-spacing: 1.5px; color: var(--offer-red); }
  .field {
    position: absolute; width: 268px; height: 42px;
    background: var(--field-white);
    border: 3px solid var(--gold);
    box-shadow: inset 0 0 0 1px var(--gold-light), 0 1px 3px rgba(0,0,0,.6);
  }
  .submit {
    position: absolute; width: 114px; height: 33px;
    background: linear-gradient(var(--button-red), var(--button-red-dark));
    border: 1px solid #5a0404; border-radius: 2px;
    box-shadow: inset 0 1px 0 rgba(255,255,255,.35), 0 2px 3px rgba(0,0,0,.6);
    font-family: 'Oswald', sans-serif; font-weight: 400; font-size: 21px;
    color: var(--ink); text-align: center; line-height: 31px;
  }
  .key-visual {
    position: absolute;
    background: radial-gradient(closest-side at 50% 50%, #f3cf6a 0%, #c8921f 40%, rgba(120,80,10,.35) 75%, rgba(120,80,10,0) 100%);
  }
  .note {
    position: absolute; top: 485px;
    font-family: 'Jost', sans-serif; font-size: 9.8px; color: var(--note-white);
    text-transform: uppercase; white-space: nowrap; letter-spacing: 0;
  }
</style>
</head>
<body>
<main class="stage">
  <svg width="0" height="0" style="position:absolute">
    <defs>
      <linearGradient id="goldFill" x1="0" y1="0" x2="0" y2="1">
        <stop offset="0" stop-color="#fff1b0"/>
        <stop offset=".35" stop-color="#d9a632"/>
        <stop offset=".55" stop-color="#fbe38e"/>
        <stop offset="1" stop-color="#9a6a12"/>
      </linearGradient>
      <linearGradient id="reflectionFade" x1="0" y1="0" x2="0" y2="1">
        <stop offset="0" stop-color="#c99a2e" stop-opacity=".28"/>
        <stop offset=".2" stop-color="#c99a2e" stop-opacity="0"/>
      </linearGradient>
    </defs>
  </svg>

  <section class="banner banner-offer">
    <svg class="headline" viewBox="0 0 600 170" aria-label="Want a great offer?">
      <text x="155" y="79" font-size="86" textLength="287" lengthAdjust="spacingAndGlyphs" fill="url(#goldFill)">WANT A</text>
      <text x="30" y="149" font-size="86" textLength="531" lengthAdjust="spacingAndGlyphs" fill="url(#goldFill)">GREAT OFFER?</text>
      <text x="30" y="-151" font-size="86" textLength="531" lengthAdjust="spacingAndGlyphs" fill="url(#reflectionFade)" transform="scale(1,-1)" aria-hidden="true">GREAT OFFER?</text>
    </svg>
    <p class="pitch pitch-lead" style="top:171px">Subscribe to our newsletter and receive a complimentary</p>
    <p class="pitch pitch-offer" style="top:194px;left:-5px">7 Night Resort/Condo - 3,500+ Locations</p>

    <div class="field" style="left:33px;top:243px"></div>
    <div class="field" style="left:33px;top:305px"></div>
    <div class="field" style="left:33px;top:363px"></div>
    <div class="submit" style="left:103px;top:421px">SUBMIT</div>

    <div class="key-visual" role="img" aria-label="Gold hotel room key with numbered key tag" style="left:331px;top:240px;width:256px;height:189px"></div>

    <p class="note" style="left:36px">We will send an email and a text mesage with the offer and how to redeem</p>
  </section>

  <section class="banner banner-contest">
    <svg class="headline" viewBox="0 0 600 170" aria-label="Enter to win!">
      <text x="31" y="95" font-size="86" textLength="529" lengthAdjust="spacingAndGlyphs" fill="url(#goldFill)">ENTER TO WIN!</text>
      <text x="31" y="-97" font-size="86" textLength="529" lengthAdjust="spacingAndGlyphs" fill="url(#reflectionFade)" transform="scale(1,-1)" aria-hidden="true">ENTER TO WIN!</text>
    </svg>
    <p class="pitch pitch-lead" style="top:124px;left:-4px">Subscribe to our newsletter and receive a complimentary</p>
    <p class="pitch pitch-offer" style="top:146px;left:-4px">7 Night Resort/Condo - 3,500+ Locations</p>

    <div class="field" style="left:33px;top:208px"></div>
    <div class="field" style="left:33px;top:269px"></div>
    <div class="field" style="left:33px;top:328px"></div>
    <div class="submit" style="left:104px;top:386px">SUBMIT</div>

    <div class="key-visual" role="img" aria-label="Gold hotel room key with numbered key tag" style="left:332px;top:205px;width:253px;height:189px"></div>

    <p class="note" style="left:36px">We will send an email and a text mesage with the offer and how to redeem</p>
  </section>
</main>
</body>
</html>
```